Kelvor Engineers: Why you should hire us keepsake

New design. Open to plastic cards. We are an engineering firm that designs cell phone towers and commercial buildings. Please check out our website www.kelvorstruct.com for more details. We want people to remember our card and for it to be useful if possible. We want the same look and feel on these cards to be translated to other marketing material we may need such as brochures.

Target Market(s)

Architects, Developers and Telecommunication Carriers

Industry/Entity Type

Engineering

Contact Information for Business Card

Card with our company colors, logo, and innovative design with elements related to our industry.

Font styles to use
Sans Serif

Colors
9bcb3c
abd036
0255a3

Requirements
Must have
• Sleek and hip design
Nice to have
• Bright lime green and navy coloring that pops with an innovative design.
Should not have
• A basic and boring design

```html
<!DOCTYPE html>
<html lang="en">
<head>
<meta charset="utf-8">
<title>Kelvor Engineers – Business Card</title>
<link href="https://fonts.googleapis.com/css2?family=Roboto:wght@300;400;500;700;900&family=Roboto+Condensed:wght@700&display=swap" rel="stylesheet">
<style>
  :root {
    --page-bg: #2a2b2d;
    --card-dark: #1c1e21;
    --card-light: #f1f1f1;
    --lime: #00ff00;
    --navy: #002b5c;
    --ink: #3a4250;
    --white: #ffffff;
    --tagline: #e8ffe0;
  }
  * { box-sizing: border-box; margin: 0; padding: 0; }
  html, body { width: 1200px; height: 960px; overflow: hidden; }
  body {
    background: var(--page-bg);
    position: relative;
    font-family: "Roboto", Arial, sans-serif;
  }
  .card {
    position: absolute;
    left: 320px;
    width: 600px;
    height: 342px;
    border-radius: 22px;
    overflow: hidden;
  }
  .card-front { top: 108px; background: var(--card-dark); }
  .card-back { top: 493px; background: var(--card-light); }

  .wordmark {
    font-family: "Roboto", Arial, sans-serif;
    font-weight: 900;
    color: var(--lime);
    letter-spacing: -2px;
    line-height: 1;
    position: absolute;
  }
  .card-front .wordmark {
    font-size: 104px;
    left: 0; right: 0; top: 112px;
    text-align: center;
  }
  .card-back .wordmark {
    font-size: 92px;
    left: 44px; top: 58px;
  }

  .tagline {
    position: absolute;
    left: 0; right: 0; top: 266px;
    display: flex; justify-content: center; align-items: center; gap: 3px;
    color: var(--tagline);
    font-weight: 700;
    font-size: 15px;
    letter-spacing: 0.3px;
  }
  .tagline .rule { width: 30px; height: 1.5px; background: var(--white); }
  .locations {
    position: absolute;
    left: 0; right: 0; top: 287px;
    text-align: center;
    color: var(--white);
    font-size: 15.5px;
    letter-spacing: 0.6px;
  }

  .swoosh { position: absolute; inset: 0; }

  .contact-list {
    position: absolute;
    right: 28px; top: 206px;
    list-style: none;
    text-align: right;
  }
  .contact-list li {
    display: flex; justify-content: flex-end; align-items: center; gap: 5px;
    font-size: 14.5px;
    font-weight: 300;
    line-height: 19.5px;
    color: var(--ink);
  }
  .contact-list svg { width: 13px; height: 13px; fill: var(--navy); }
  .person-name {
    position: absolute;
    right: 28px; top: 294px;
    font-family: "Roboto Condensed", Arial, sans-serif;
    font-weight: 700;
    font-size: 21px;
    color: var(--navy);
    letter-spacing: 0.2px;
  }
</style>
</head>
<body>

  <section class="card card-front">
    <div class="wordmark">KELVOR</div>
    <div class="tagline"><span class="rule"></span>MULTI-DISCIPLINE ENGINEERING<span class="rule"></span></div>
    <div class="locations">Denver | Raleigh | Phoenix | Salt Lake City</div>
  </section>

  <section class="card card-back">
    <svg class="swoosh" viewBox="0 0 600 342" width="600" height="342" aria-hidden="true">
      <path d="M420 0 C520 40 440 190 305 250 C470 182 560 110 580 0 Z" fill="var(--navy)"/>
      <path d="M100 342 C300 280 525 170 583 0 L600 0 L600 342 Z" fill="var(--lime)" stroke="var(--white)" stroke-width="4"/>
    </svg>

    <div class="wordmark">KELVOR</div>

    <ul class="contact-list">
      <li>555.014.7731
        <svg viewBox="0 0 16 16"><path d="M3.5 1 L6 1 L7 4.5 L5.3 5.8 C6.2 7.8 8.2 9.8 10.2 10.7 L11.5 9 L15 10 L15 12.5 C15 13.9 13.9 15 12.5 15 C6.2 15 1 9.8 1 3.5 C1 2.1 2.1 1 3.5 1 Z"/></svg>
      </li>
      <li>555.019.4460
        <svg viewBox="0 0 16 16"><path d="M4 0 H12 A1.5 1.5 0 0 1 13.5 1.5 V14.5 A1.5 1.5 0 0 1 12 16 H4 A1.5 1.5 0 0 1 2.5 14.5 V1.5 A1.5 1.5 0 0 1 4 0 Z M4.5 2 V12.5 H11.5 V2 Z M8 13.3 A0.9 0.9 0 1 0 8 15.1 A0.9 0.9 0 1 0 8 13.3 Z"/></svg>
      </li>
      <li>dreyes@kelvorstruct.com
        <svg viewBox="0 0 16 16"><path d="M1 3 H15 V4 L8 8.5 L1 4 Z M1 5.5 L8 10 L15 5.5 V13 H1 Z"/></svg>
      </li>
      <li>www.kelvorstruct.com
        <svg viewBox="0 0 16 16"><path d="M8 1 A7 7 0 1 0 8 15 A7 7 0 1 0 8 1 Z M5 4 C6.5 4 7 5.5 6 6.5 C5 7.5 6.5 9 5.5 10.5 C4.8 11.5 3.2 10 3 8 C2.8 6 3.8 4 5 4 Z M10 3.5 C11.5 4 13 6 12.8 8.5 C12.6 10.5 11 12.5 10 11.5 C9 10.5 10.5 9 9.5 7.5 C8.5 6 9 4 10 3.5 Z"/></svg>
      </li>
    </ul>
    <div class="person-name">DANA HOLLOWAY REYES</div>
  </section>

</body>
</html>
```